Coffee House With Cycling Theme Wants Business Cards

We want to create a business card for a coffee house that has a cycling theme. We expect to use the current logo on one side of the business card and we have been considering adding the words 'COFFEE HOUSE' underneath (see example). For the other side of the business card we want an interesting design with tag-line, address and social media links (the normal business card stuff). See examples provided but we are not fixed on having it exactly as shown, we are very open to great creative ideas. Please note our logo has the initials ‘KR' in orange embedded in the design and this must be retained. However, you can play with the words COFFEE HOUSE as well as use the orange color on the backside of the business card, as you see fit. For an image on the backside of the business card it can be a photo, hand-drawn or whatever but it must visually combine coffee and cycling in some way. The interior of the Coffee House will be reclaimed wood, rustic and have an urban feel to it with cycling artifacts hanging from the walls/ceiling, etc. Finally, it would be beneficial if the business card design elements can be easily used on flyers and other promotional assets. Good luck, we are looking forward to seeing your creative ideas.

Target Market(s)

Coffee lovers and cycling fans

Contact Information for Business Card

See project description.

Colors

Designer to choose colors to be used in the design.

Requirements
Must have
• Must use the current logo provided and combine a coffee and bike theme.
Nice to have
• Orange is used in current logo and could be used as an accent color on the backside of the business card.

```html
<!DOCTYPE html>
<html lang="en">
<head>
<meta charset="utf-8">
<title>KR Coffee House – Business Card</title>
<link href="https://fonts.googleapis.com/css2?family=Lato:wght@400;700&family=Open+Sans:wght@400;600&display=swap" rel="stylesheet">
<style>
  :root {
    --backdrop: #5a5a5a;
    --card-light: #efefef;
    --charcoal: #3d3d3d;
    --orange: #ff6a1f;
    --ink: #333333;
    --white: #ffffff;
  }
  html, body {
    margin: 0;
    width: 1200px;
    height: 1200px;
    overflow: hidden;
    background: var(--backdrop);
  }
  .stage { position: relative; width: 1200px; height: 1200px; }

  .card-front {
    position: absolute;
    left: 234px; top: 310px;
    width: 364px; height: 594px;
    display: flex; flex-direction: column;
    box-shadow: 2px 3px 6px rgba(0,0,0,.45);
  }
  .brand-panel {
    height: 363px;
    background: var(--card-light);
    text-align: center;
    position: relative;
  }
  .brand-mark {
    position: absolute; left: 0; right: 0; top: 80px;
    font-family: "Lato", sans-serif;
    font-weight: 700;
    font-size: 120px;
    line-height: 1;
    color: var(--orange);
  }
  .brand-name {
    position: absolute; left: 0; right: 0; top: 243px;
    font-family: "Lato", sans-serif;
    font-size: 36px;
    color: var(--orange);
  }
  .brand-web {
    position: absolute; left: 0; right: 0; top: 299px;
    font-family: "Open Sans", sans-serif;
    font-size: 19px;
    color: var(--ink);
  }
  .tagline-band {
    height: 113px;
    background: var(--charcoal);
    text-align: center;
    font-family: "Lato", sans-serif;
  }
  .tagline-title {
    margin: 24px 0 0;
    font-size: 34px;
    font-weight: 700;
    color: var(--orange);
    line-height: 40px;
  }
  .tagline-sub {
    margin: 0;
    font-size: 20px;
    color: var(--white);
    line-height: 30px;
  }
  .address-band {
    flex: 1;
    display: flex; flex-direction: column; justify-content: center;
    padding-bottom: 14px;
    background: var(--orange);
    text-align: center;
    font-family: "Open Sans", sans-serif;
    font-weight: 600;
    font-size: 17px;
    line-height: 24px;
    color: var(--white);
  }

  .card-back {
    position: absolute;
    left: 627px; top: 310px;
    width: 370px; height: 596px;
    box-shadow: 2px 3px 6px rgba(0,0,0,.45);
    overflow: hidden;
  }
  .hero-photo {
    position: absolute; inset: 0;
    background: linear-gradient(180deg,
      #4a2a18 0%, #5e3620 30%, #8a5530 50%, #c89060 60%,
      #6b4a2c 68%, #b08a55 74%, #7a8a3a 84%, #3e4a2a 93%, #1f2a30 100%);
  }
  .social-dot {
    position: absolute; left: 63px; top: 505px;
    width: 34px; height: 34px; border-radius: 50%;
    background: var(--white);
  }
  .social-handle {
    position: absolute; left: 41px; top: 546px;
    font-family: "Open Sans", sans-serif;
    font-size: 20px;
    line-height: 28px;
    color: var(--white);
  }
</style>
</head>
<body>
<main class="stage">
  <section class="card-front">
    <div class="brand-panel">
      <div class="brand-mark">KR</div>
      <div class="brand-name">COFFEE HOUSE</div>
      <div class="brand-web">www.krcoffeehouse.com</div>
    </div>
    <div class="tagline-band">
      <p class="tagline-title">CUPS &amp; CRANKS</p>
      <p class="tagline-sub">FUEL YOUR NEXT RIDE</p>
    </div>
    <div class="address-band">
      <span>501, Address Goes Here</span>
      <span>Country Name, 123456</span>
    </div>
  </section>

  <section class="card-back">
    <div class="hero-photo" role="img" aria-label="Photo of roasted coffee beans above a steaming white cup of coffee, blending into a green hillside road with a cyclist riding away"></div>
    <span class="social-dot"></span>
    <span class="social-handle">krcoffeehouse</span>
  </section>
</main>
</body>
</html>
```